Modern, clean business card for Clearbrook Optics

Updated business card with a modern look.

Logo on the front
Dr Tavin R Marquell and Associates on the front.
Three locations on the back:
Ridgefront Brantmart
509-555-0142
18342 E Fernhollow Ave

Pelham Brantmart
509-555-0187
4716 W Dunmore Ave

Copper Bluff Brantmart
509-555-0163
3854 S Kettering Rd

Facebook icon. www.clearbrookoptix.example

Nice open white space on back for writing next appointment time.

Target Market(s)

Main target is female 25-50, but I would like broad appeal.

Industry/Entity Type

Healthcare

Contact Information for Business Card

Modern look

Font styles to use
Serif

Requirements
Must have
• Logo and Dr Tavin R Marquell and Associates on front.
• 3 locations on back
• white space for noting next appointment

```html
<!DOCTYPE html>
<html lang="en">
<head>
<meta charset="utf-8">
<title>Clearbrook Optics – Business Card</title>
<link rel="stylesheet" href="https://fonts.googleapis.com/css2?family=Open+Sans:ital,wght@0,400;0,600;0,700;1,400&family=PT+Sans+Narrow:wght@700&display=swap">
<style>
  :root {
    --backdrop: #5e5e5e;
    --card: #ffffff;
    --navy: #1d3d6e;
    --blue: #1f6db5;
    --blue-dark: #12468a;
    --grey-text: #555555;
    --grey-band: #b9b9b9;
    --dots: #8a8a8a;
  }
  * { box-sizing: border-box; margin: 0; padding: 0; }
  html, body { width: 1105px; height: 1200px; overflow: hidden; }
  body {
    background: var(--backdrop);
    font-family: "Open Sans", Arial, sans-serif;
    position: relative;
  }
  .card {
    position: absolute;
    left: 196px;
    width: 720px;
    height: 412px;
    background: var(--card);
    box-shadow: 0 3px 8px rgba(0,0,0,0.45);
    overflow: hidden;
  }
  .card--front { top: 146px; }
  .card--back { top: 602px; }

  /* front */
  .practice-name {
    position: absolute; left: 39px; top: 70px;
    font-family: "PT Sans Narrow", "Arial Narrow", sans-serif;
    font-weight: 700; font-size: 37px; color: var(--navy);
  }
  .locations { position: absolute; left: 39px; top: 172px; list-style: none; }
  .location { margin-bottom: 12px; line-height: 26px; }
  .location__name { font-weight: 600; font-size: 19px; color: #333; display: block; }
  .location__detail { font-size: 18.5px; color: var(--grey-text); display: block; }
  .social-square {
    position: absolute; left: 674px; top: 19px; width: 27px; height: 27px;
    background: var(--blue);
  }
  .brand { position: absolute; left: 398px; top: 272px; width: 282px; text-align: center; }
  .brand__name {
    font-weight: 700; font-size: 27px; color: var(--navy); letter-spacing: 0.5px; line-height: 34px;
  }
  .brand__tagline {
    font-weight: 700; font-size: 13px; color: var(--navy); letter-spacing: 0.5px;
  }
  .footer-band { position: absolute; left: 0; bottom: 0; width: 720px; height: 25px; }
  .footer-band svg { display: block; }
  .web-address {
    position: absolute; right: 44px; bottom: 2px;
    font-weight: 700; font-size: 15px; color: #fff; letter-spacing: 3.2px;
  }

  /* back */
  .appt-title {
    position: absolute; left: 0; right: 0; top: 34px; text-align: center;
    font-weight: 600; font-size: 27px; color: var(--navy);
  }
  .appt-row {
    position: absolute; display: flex; align-items: baseline; color: var(--navy);
  }
  .fill-line {
    display: inline-block; border-bottom: 2px dotted var(--dots); height: 1px; margin-right: 10px;
  }
  .appt-row--patient { left: 43px; top: 110px; color: var(--grey-text); font-size: 18.5px; }
  .appt-row--when { left: 35px; top: 180px; font-size: 20px; }
  .appt-row--when .label + .fill-line { margin-left: 12px; }
  .ampm { font-size: 13px; margin-left: -6px; }
  .weekdays {
    position: absolute; left: 40px; top: 260px; width: 650px;
    display: flex; justify-content: space-between; list-style: none;
    font-size: 18.5px; color: var(--navy);
  }
  .weekday { display: flex; align-items: center; }
  .tick-box {
    display: inline-block; width: 20px; height: 18px; border: 1.5px solid #444; margin-left: 8px;
  }
  .notice {
    position: absolute; left: 0; right: 0; top: 336px; text-align: center;
    font-style: italic; font-size: 15px; line-height: 21px; color: var(--grey-text);
  }
</style>
</head>
<body>
  <section class="card card--front">
    <h1 class="practice-name">Dr Tavin R Marquell &amp; Associates</h1>
    <span class="social-square" aria-label="Social page"></span>
    <ul class="locations">
      <li class="location">
        <span class="location__name">Ridgefront Brantmart</span>
        <span class="location__detail">509-555-0142, 18342 E Fernhollow Ave</span>
      </li>
      <li class="location">
        <span class="location__name">Pelham Brantmart</span>
        <span class="location__detail">509-555-0187, 4716 W Dunmore Ave</span>
      </li>
      <li class="location">
        <span class="location__name">Copper Bluff Brantmart</span>
        <span class="location__detail">509-555-0163, 3854 S Kettering Rd</span>
      </li>
    </ul>
    <div class="brand">
      <div class="brand__name">CLEARBROOK OPTICS</div>
      <div class="brand__tagline">ADVANCED EYE CARE</div>
    </div>
    <div class="footer-band">
      <svg width="720" height="25" viewBox="0 0 720 25">
        <defs>
          <linearGradient id="bandBlue" x1="0" x2="1" y1="0" y2="0">
            <stop offset="0" stop-color="#12468a"/>
            <stop offset="1" stop-color="#1f6db5"/>
          </linearGradient>
        </defs>
        <rect x="0" y="0" width="360" height="25" fill="#b9b9b9"/>
        <polygon points="357,0 720,0 720,25 333,25" fill="#ffffff"/>
        <polygon points="362,0 720,0 720,25 338,25" fill="url(#bandBlue)"/>
      </svg>
      <span class="web-address">www.clearbrookoptix.example</span>
    </div>
  </section>

  <section class="card card--back">
    <h2 class="appt-title">Next Appointment</h2>
    <div class="appt-row appt-row--patient">
      <span class="fill-line" style="width:418px"></span>
      <span>has an apppointment</span>
    </div>
    <div class="appt-row appt-row--when">
      <span class="label">Date :</span>
      <span class="fill-line" style="width:272px"></span>
      <span class="label" style="margin-left:14px">Time :</span>
      <span class="fill-line" style="width:150px;margin-left:8px"></span>
      <span class="ampm">AM/PM</span>
    </div>
    <ul class="weekdays">
      <li class="weekday">Sun<span class="tick-box"></span></li>
      <li class="weekday">Mon<span class="tick-box"></span></li>
      <li class="weekday">Tue<span class="tick-box"></span></li>
      <li class="weekday">Wed<span class="tick-box"></span></li>
      <li class="weekday">Thu<span class="tick-box"></span></li>
      <li class="weekday">Fri<span class="tick-box"></span></li>
      <li class="weekday">Sat<span class="tick-box"></span></li>
    </ul>
    <p class="notice">Please give me 24 hours notice if you are unable to keep your appointment or<br>a cancellation fee may be charged.</p>
  </section>
</body>
</html>
```